Brightmill Data Works

Our company is about IT hardwares and IT solutions. IT hardware such as PC, RAMS, storage and servers. IT solutions such as project management, BA. We are also selling new technology too.

Target Market(s)

Consumer, Small to Medium Business, Corporate

Requirements
Must have
• The business card must have the following:
• Name:
• Title:
• Contact Number:
• Email address:
• Website:
• Color: Must match the logo color upgrade

```html
<!DOCTYPE html>
<html lang="en">
<head>
<meta charset="UTF-8">
<title>Brightmill Data Works — Business Card</title>
<link rel="stylesheet" href="https://fonts.googleapis.com/css2?family=Open+Sans:wght@400;600;700&display=swap">
<style>
  :root {
    --backdrop: #e7e5e2;
    --card: #474747;
    --accent: #c97a2a;
    --accent-soft: #e0963f;
    --text-light: #f2f2f2;
    --text-muted: #e4e4e4;
  }
  * { box-sizing: border-box; margin: 0; padding: 0; }
  html, body {
    width: 1200px;
    height: 997px;
    overflow: hidden;
    background: var(--backdrop);
    font-family: "Open Sans", Arial, sans-serif;
  }
  .sheet {
    width: 1200px;
    height: 997px;
    display: flex;
    flex-direction: column;
    align-items: center;
    justify-content: center;
    gap: 56px;
  }
  .card {
    position: relative;
    width: 700px;
    height: 400px;
    background: var(--card);
    border-radius: 4px;
    box-shadow: 0 10px 26px rgba(0, 0, 0, 0.18);
    overflow: hidden;
  }

  /* Front */
  .card--front {
    display: flex;
    align-items: center;
    justify-content: center;
  }
  .brand {
    display: flex;
    align-items: center;
    gap: 18px;
  }
  .brand__square {
    width: 30px;
    height: 30px;
    background: var(--accent);
  }
  .brand__name {
    font-weight: 700;
    font-size: 34px;
    letter-spacing: 1px;
    color: var(--text-light);
    text-transform: uppercase;
  }

  /* Back */
  .circuit-band {
    position: absolute;
    left: 0;
    top: 0;
    width: 100%;
    height: 210px;
    background: linear-gradient(180deg,
      rgba(201, 122, 42, 0.38) 0%,
      rgba(201, 122, 42, 0.22) 55%,
      rgba(201, 122, 42, 0) 100%);
  }
  .contact {
    position: absolute;
    right: 48px;
    top: 205px;
    text-align: right;
    color: var(--text-muted);
    font-size: 15px;
    line-height: 21px;
    list-style: none;
  }
  .person {
    position: absolute;
    left: 48px;
    bottom: 58px;
  }
  .person__name {
    color: var(--accent-soft);
    font-weight: 600;
    font-size: 26px;
    text-transform: uppercase;
    line-height: 1.1;
  }
  .person__title {
    color: var(--text-light);
    font-weight: 600;
    font-size: 15px;
    text-transform: uppercase;
    margin-top: 2px;
  }
</style>
</head>
<body>
  <main class="sheet">
    <section class="card card--front" aria-label="Card front">
      <div class="brand">
        <span class="brand__square"></span>
        <span class="brand__name">Brightmill Data Works</span>
      </div>
    </section>

    <section class="card card--back" aria-label="Card back">
      <div class="circuit-band" role="img" aria-label="Glowing orange circuit-trace pattern running down from the top edge"></div>
      <ul class="contact">
        <li>555 214 7390</li>
        <li>daniel@brightmilldata.com</li>
        <li>www.brightmilldata.com</li>
      </ul>
      <div class="person">
        <p class="person__name">Daniel Reyes</p>
        <p class="person__title">CEO/Founder</p>
      </div>
    </section>
  </main>
</body>
</html>
```